Ward Compass Business Card Design*

We need a business card design for our company Ward Compass. Our company is specialized in providing online consulting services regarding medical institutions, hospitals and doctors. We work with patients worldwide looking to choose between healthcare providers. We have a website you may use as a reference, where we list doctors and clinics worldwide. So we target Medical providers as well as patients worldwide.
Target Market(s)
Medical Providers and patients around the world
Industry/Entity Type
Medical
Contact Information for Business Card
Salwa Kettani
CEO
+90 612 348 2175
info@wardcompass.example
www.wardcompass.example
14 Annakhil 7 H.R.B. Rabat, Morocco
Requirements
Must have
- Company logo/name on one full side, personal info and smaller logo and company name on the other side.
Nice to have
- Smart and elegant design

```html
<!DOCTYPE html>
<html lang="en">
<head>
<meta charset="utf-8">
<title>Ward Compass Business Card</title>
<link href="https://fonts.googleapis.com/css2?family=Open+Sans:wght@400;600;700&display=swap" rel="stylesheet">
<style>
  :root {
    --page-bg: #e6e4e0;
    --brand-blue: #2c4878;
    --strip-white: #f2f2f2;
    --info-grey: #58595b;
    --name-blue: #2c4878;
    --name-grey: #6d6e71;
    --text-white: #ffffff;
    --text-soft: #d9dde6;
    --mark-grey: #c9ccd2;
  }
  * { margin: 0; padding: 0; box-sizing: border-box; }
  html, body { width: 900px; height: 1200px; overflow: hidden; }
  body {
    background: var(--page-bg);
    font-family: "Open Sans", Arial, sans-serif;
    position: relative;
  }
  .card {
    position: absolute;
    left: 70px;
    width: 760px;
    height: 434px;
    overflow: hidden;
    box-shadow: 0 6px 18px rgba(0,0,0,0.25);
  }
  .card--front { top: 140px; }
  .card--back { top: 626px; background: var(--brand-blue); }

  .front-brand {
    position: absolute; top: 0; left: 0; right: 0; height: 246px;
    background: var(--brand-blue);
    display: flex; align-items: center; justify-content: center;
  }
  .brand-lockup { display: flex; align-items: center; gap: 18px; }
  .brand-dot {
    width: 62px; height: 62px; border-radius: 50%;
    background: var(--mark-grey);
  }
  .brand-name {
    color: var(--text-white);
    font-weight: 600;
    font-size: 40px;
    letter-spacing: 1px;
    text-transform: uppercase;
  }

  .name-strip {
    position: absolute; top: 246px; left: 0; right: 0; height: 50px;
    background: var(--strip-white);
    display: flex; align-items: center;
    padding-left: 30px;
  }
  .person-name { font-size: 20px; letter-spacing: 0.5px; text-transform: uppercase; }
  .person-name .first { color: var(--name-blue); font-weight: 700; }
  .person-name .last { color: var(--name-grey); font-weight: 400; }
  .person-title {
    margin-left: 16px; font-size: 11px; color: var(--name-grey);
    text-transform: uppercase; letter-spacing: 0.5px;
  }

  .contact-panel {
    position: absolute; top: 296px; left: 0; right: 0; bottom: 0;
    background: var(--info-grey);
    color: var(--text-white);
    font-size: 15px;
  }
  .contact-list { position: absolute; left: 34px; top: 34px; list-style: none; }
  .contact-list li { display: flex; align-items: center; gap: 14px; height: 26px; }
  .contact-list svg { width: 15px; height: 15px; fill: var(--text-white); }
  .address {
    position: absolute; left: 466px; top: 34px;
    font-style: normal; line-height: 26px;
  }

  .back-brand {
    position: absolute; left: 0; right: 0; top: 150px;
    display: flex; justify-content: center;
  }
  .website {
    position: absolute; left: 0; right: 0; bottom: 26px;
    text-align: center; color: var(--text-soft);
    font-size: 13px; letter-spacing: 3px;
  }
</style>
</head>
<body>
  <section class="card card--front">
    <div class="front-brand">
      <div class="brand-lockup">
        <span class="brand-dot"></span>
        <span class="brand-name">Ward Compass</span>
      </div>
    </div>
    <div class="name-strip">
      <span class="person-name"><span class="first">Salwa</span> <span class="last">Kettani</span></span>
      <span class="person-title">CEO</span>
    </div>
    <div class="contact-panel">
      <ul class="contact-list">
        <li>
          <svg viewBox="0 0 24 24" aria-hidden="true"><path d="M6.6 10.8a15.1 15.1 0 0 0 6.6 6.6l2.2-2.2c.3-.3.7-.4 1-.2 1.1.4 2.3.6 3.6.6.6 0 1 .4 1 1V20c0 .6-.4 1-1 1A17 17 0 0 1 3 4c0-.6.4-1 1-1h3.5c.6 0 1 .4 1 1 0 1.3.2 2.5.6 3.6.1.3 0 .7-.2 1z"/></svg>
          <span>+90 612 348 2175</span>
        </li>
        <li>
          <svg viewBox="0 0 24 24" aria-hidden="true"><path d="M2 5h20v14H2z M2 5l10 8 10-8" /></svg>
          <span>info@wardcompass.example</span>
        </li>
      </ul>
      <address class="address">14 Annakhil 7 H.R.B.<br>Rabat, Morocco</address>
    </div>
  </section>

  <section class="card card--back">
    <div class="back-brand">
      <div class="brand-lockup">
        <span class="brand-dot"></span>
        <span class="brand-name">Ward Compass</span>
      </div>
    </div>
    <p class="website">www.wardcompass.example</p>
  </section>
</body>
</html>
```